Create a Powerpoint presentation pack with our new logo

We have just selected a new logo using ArtworkHive and we were wanting to create a new Powerpoint presentation pack using this logo.
We'd like the powerpoint pack to have a title page + a header and footer page.
We would like the logo to appear on the title page and the header / footer page.
We are flexible with colours and want something that reflects an IT / travel flair.

I have attached the logo that we just selected from the artworkhive page.

Larkspan Digital Systems is the IT division of Larkspan Journeys Holdings which is the largest travel retailer in Australia. We have offices in the US, Canada, UK, Singapore, Hong Kong, UAE, India, South Africa, Mexico and New Zealand.

```html
<!DOCTYPE html>
<html lang="en">
<head>
<meta charset="utf-8">
<title>Larkspan Digital Systems – Extra Slides</title>
<link href="https://fonts.googleapis.com/css2?family=Raleway:wght@400;600;700;800&display=swap" rel="stylesheet">
<style>
:root{
  --red:#e8202a;
  --black:#111111;
  --dark:#4a4a4a;
  --mid:#7d7d7d;
  --light:#b7b7b7;
  --pale:#ececec;
  --paper:#ffffff;
  --ink:#222222;
  --muted:#8a8a8a;
  --bg:#e9e9e9;
}
*{box-sizing:border-box;margin:0;padding:0}
html,body{width:1200px;height:690px;overflow:hidden;background:var(--bg);font-family:'Raleway',sans-serif;color:var(--ink)}
.deck{position:relative;width:1200px;height:690px}
.slide{position:absolute;width:394px;height:220px;background:var(--paper);overflow:hidden;box-shadow:0 1px 3px rgba(0,0,0,.18)}
.abs{position:absolute}
.slide-title{position:absolute;left:16px;top:17px;font-size:12.5px;font-weight:800;letter-spacing:.1px;color:var(--black)}
.slide-title::after{content:"";position:absolute;left:0;top:20px;width:22px;height:2px;background:var(--red)}
.brand{position:absolute;right:12px;top:12px;display:flex;flex-direction:column;align-items:center;gap:2px}
.brand-dot{width:11px;height:11px;border-radius:50%;background:var(--red)}
.brand-name{font-size:5.5px;font-weight:700;color:var(--red);letter-spacing:.3px}
.copyright{position:absolute;left:8px;bottom:7px;font-size:3.8px;color:var(--muted)}
.page-no{position:absolute;right:8px;bottom:5px;width:11px;height:11px;border-radius:50%;background:var(--red);color:#fff;font-size:4px;display:flex;align-items:center;justify-content:center}
.tiny{font-size:4.3px;line-height:1.45;color:#555}
.box-head{height:10px;font-size:5px;font-weight:700;color:#fff;display:flex;align-items:center;justify-content:center}
.box-body{background:var(--pale);padding:4px 3px;text-align:center}
.bg-black{background:var(--black)}.bg-dark{background:var(--dark)}.bg-mid{background:var(--mid)}.bg-light{background:var(--light)}.bg-red{background:var(--red)}
.line{position:absolute;background:#9a9a9a}
.node{position:absolute;height:15px;font-size:4.6px;color:#fff;display:flex;align-items:center;justify-content:center;text-align:center;line-height:1.1}
.pct{font-weight:400;color:#444}
.pct b{font-weight:700;font-size:5.5px;color:#222}
.red{color:var(--red)}
</style>
</head>
<body>
<main class="deck">

<!-- Title slide -->
<section class="slide" style="left:4px;top:5px;background:#1b1c20">
  <div class="abs" role="img" aria-label="Dark night photograph of a passenger jet in flight" style="inset:0;background:radial-gradient(ellipse at 45% 40%,#3b3d44 0%,#24262b 50%,#151619 100%)"></div>
  <div class="abs" style="left:10px;top:16px;width:190px;height:190px;border-radius:50%;border:14px solid rgba(255,255,255,.07)"></div>
  <div class="abs" style="right:20px;top:28px;display:flex;flex-direction:column;align-items:center;gap:4px">
    <div class="brand-dot" style="width:20px;height:20px"></div>
    <div style="font-size:10px;font-weight:700;color:#fff;letter-spacing:.5px">LARKSPAN</div>
  </div>
  <div class="abs" style="right:24px;top:144px;font-size:22px;font-weight:700;color:#fff">EXTRA SLIDES</div>
  <div class="abs" style="left:0;top:175px;width:300px;height:1px;background:var(--red);opacity:.7"></div>
  <div class="abs" style="right:24px;top:171px;font-size:7px;color:var(--red)">Your Subtitle Goes Here</div>
</section>

<!-- Org chart A -->
<section class="slide" style="left:402px;top:5px">
  <h2 class="slide-title">ORG CHARTS</h2>
  <div class="brand"><span class="brand-dot"></span><span class="brand-name">LARKSPAN</span></div>
  <div class="abs bg-red box-head" style="left:26px;top:48px;width:340px;height:14px;font-size:6.5px;font-weight:600">Description</div>
  <div class="abs box-body tiny" style="left:26px;top:64px;width:340px;height:32px;padding-top:8px">There are many variations of passages of Lorem Ipsum available, but the majority have suffered alteration in some<br>form, or randomized words which don't look even slightly believable.</div>
  <div class="line" style="left:196px;top:96px;width:1px;height:8px"></div>
  <div class="line" style="left:61px;top:104px;width:271px;height:1px"></div>
  <div class="abs" style="left:26px;top:108px;width:340px;display:grid;grid-template-columns:repeat(4,1fr);gap:12px 12px">
    <div><div class="box-head bg-black">Description</div><div class="box-body tiny"><b>Suitable for all categories</b><br>business and personal presentation.</div></div>
    <div><div class="box-head bg-dark">Description</div><div class="box-body tiny"><b>Suitable for all categories</b><br>business and personal presentation.</div></div>
    <div><div class="box-head bg-mid">Description</div><div class="box-body tiny"><b>Suitable for all categories</b><br>business and personal presentation.</div></div>
    <div><div class="box-head bg-light">Description</div><div class="box-body tiny"><b>Suitable for all categories</b><br>business and personal presentation.</div></div>
    <div><div class="box-head bg-black">Description</div><div class="box-body tiny"><b>Suitable for all categories</b><br>business and personal presentation.</div></div>
    <div><div class="box-head bg-dark">Description</div><div class="box-body tiny"><b>Suitable for all categories</b><br>business and personal presentation.</div></div>
    <div><div class="box-head bg-mid">Description</div><div class="box-body tiny"><b>Suitable for all categories</b><br>business and personal presentation.</div></div>
    <div><div class="box-head" style="background:#d4d4d4">Description</div><div class="box-body tiny"><b>Suitable for all categories</b><br>business and personal presentation.</div></div>
  </div>
  <p class="copyright">© Copyright 2017 Larkspan Digital Systems. All rights reserved.</p>
  <span class="page-no">59</span>
</section>

<!-- Org chart B -->
<section class="slide" style="left:800px;top:5px">
  <h2 class="slide-title">ORG CHARTS</h2>
  <div class="brand"><span class="brand-dot"></span><span class="brand-name">LARKSPAN</span></div>
  <div class="abs" style="left:22px;top:80px;width:107px">
    <div class="box-head bg-red" style="height:16px;font-size:6.5px;font-weight:600">Description</div>
    <div class="box-body tiny" style="padding:6px 5px">There are many variations of passages of Lorem Ipsum available, but the majority have suffered alteration in some form, or randomized words which don't look even slightly believable.</div>
  </div>
  <div class="line" style="left:129px;top:130px;width;width:12px;height:1px"></div>
  <div class="line" style="left:141px;top:80px;width:1px;height:96px"></div>
  <div class="abs" style="left:150px;top:46px;width:232px;display:grid;grid-template-columns:1fr 1fr;gap:26px 11px">
    <div><div class="box-head bg-black" style="height:13px;font-size:5.5px">Description</div><div class="box-body tiny" style="padding:5px">There are many variations of passages of Lorem Ipsum available, but the majority have suffered alteration in some form.</div></div>
    <div><div class="box-head bg-mid" style="height:13px;font-size:5.5px">Description</div><div class="box-body tiny" style="padding:5px">There are many variations of passages of Lorem Ipsum available, but the majority have suffered alteration in some form.</div></div>
    <div><div class="box-head bg-mid" style="height:13px;font-size:5.5px">Description</div><div class="box-body tiny" style="padding:5px">There are many variations of passages of Lorem Ipsum available, but the majority have suffered alteration in some form.</div></div>
    <div><div class="box-head bg-light" style="height:13px;font-size:5.5px">Description</div><div class="box-body tiny" style="padding:5px">There are many variations of passages of Lorem Ipsum available, but the majority have suffered alteration in some form.</div></div>
  </div>
  <p class="copyright">© Copyright 2017 Larkspan Digital Systems. All rights reserved.</p>
  <span class="page-no">60</span>
</section>

<!-- Company structure -->
<section class="slide" style="left:4px;top:236px">
  <h2 class="slide-title">COMPANY STRUCTURE</h2>
  <div class="brand"><span class="brand-dot"></span><span class="brand-name">LARKSPAN</span></div>
  <div class="node bg-red" style="left:167px;top:53px;width:58px">General Manager</div>
  <div class="line" style="left:196px;top:68px;width:1px;height:10px"></div>
  <div class="line" style="left:107px;top:78px;width:178px;height:1px"></div>
  <div class="line" style="left:107px;top:78px;width:1px;height:12px"></div>
  <div class="line" style="left:196px;top:78px;width:1px;height:12px"></div>
  <div class="line" style="left:285px;top:78px;width:1px;height:12px"></div>
  <div class="node bg-black" style="left:78px;top:90px;width:58px;height:18px">Asistant Manager</div>
  <div class="node bg-black" style="left:167px;top:90px;width:58px;height:18px">Asistant Manager</div>
  <div class="node bg-black" style="left:256px;top:90px;width:58px;height:18px">Asistant Manager</div>
  <div class="line" style="left:196px;top:108px;width:1px;height:13px"></div>
  <div class="line" style="left:67px;top:121px;width:266px;height:1px"></div>
  <div class="line" style="left:67px;top:121px;width:1px;height:10px"></div>
  <div class="line" style="left:156px;top:121px;width:1px;height:10px"></div>
  <div class="line" style="left:244px;top:121px;width:1px;height:10px"></div>
  <div class="line" style="left:333px;top:121px;width:1px;height:10px"></div>
  <div class="node bg-dark" style="left:38px;top:131px;width:58px;height:19px">Department<br>of Commerce</div>
  <div class="node bg-mid" style="left:127px;top:131px;width:58px;height:19px">Financial<br>Department</div>
  <div class="node bg-mid" style="left:215px;top:131px;width:58px;height:19px">Administrative<br>Department</div>
  <div class="node bg-dark" style="left:304px;top:131px;width:58px;height:19px">Workshop</div>
  <p class="copyright">© Copyright 2017 Larkspan Digital Systems. All rights reserved.</p>
  <span class="page-no">61</span>
</section>

<!-- Plane infographic A -->
<section class="slide" style="left:402px;top:236px">
  <h2 class="slide-title">PLANE INFOGRAPHIC</h2>
  <div class="brand"><span class="brand-dot"></span><span class="brand-name">LARKSPAN</span></div>
  <div class="abs" role="img" aria-label="Side-view airliner illustration split into grey, black and red segments" style="left:28px;top:52px;width:350px;height:62px;border-radius:30px 8px 8px 30px;background:linear-gradient(90deg,var(--light) 0 46%,var(--black) 46% 80%,var(--red) 80%)"></div>
  <div class="abs pct" style="left:50px;top:126px;font-size:18px;font-weight:300">40%<b style="font-size:6px"> followers</b></div>
  <p class="abs tiny" style="left:50px;top:150px;width:76px;font-size:3.8px">of followers agree that they are got a good information and service from us, and refer it to their friend's</p>
  <div class="abs pct" style="left:162px;top:159px;font-size:18px;font-weight:300">35%<b style="font-size:6px"> followers</b></div>
  <p class="abs tiny" style="left:162px;top:183px;width:76px;font-size:3.8px">of followers agree that they are got a good information and service from us, and refer it to their friend's</p>
  <div class="abs pct red" style="left:267px;top:116px;font-size:18px;font-weight:300">25%<b style="font-size:6px"> followers</b></div>
  <p class="abs tiny" style="left:267px;top:140px;width:76px;font-size:3.8px">of followers agree that they are got a good information and service from us, and refer it to their friend's</p>
  <p class="copyright">© Copyright 2017 Larkspan Digital Systems. All rights reserved.</p>
  <span class="page-no">62</span>
</section>

<!-- Plane infographic B -->
<section class="slide" style="left:800px;top:236px">
  <h2 class="slide-title">PLANE INFOGRAPHIC</h2>
  <div class="brand"><span class="brand-dot"></span><span class="brand-name">LARKSPAN</span></div>
  <div class="abs" role="img" aria-label="Front-view airliner illustration with red, black and grey wings" style="left:26px;top:132px;width:346px;height:72px;background:linear-gradient(90deg,var(--red) 0 22%,var(--black) 22% 46%,var(--dark) 46% 62%,var(--light) 62%);clip-path:polygon(0 38%,100% 38%,100% 52%,62% 60%,62% 100%,46% 100%,46% 60%,0 52%)"></div>
  <div class="abs" style="left:40px;top:70px;text-align:center;width:40px"><div style="width:18px;height:12px;margin:0 auto 2px;background:linear-gradient(90deg,var(--red) 25%,#fff 25% 75%,var(--red) 75%);border:1px solid #ddd"></div><div style="font-size:5px;font-weight:700">Description</div><div class="red" style="font-size:10px">9%</div><div class="tiny" style="font-size:3.5px">Just change the chart, and recolor a fill with your own.</div></div>
  <div class="line" style="left:60px;top:124px;width:1px;height:35px;background:var(--red)"></div>
  <div class="abs" style="left:96px;top:50px;text-align:center;width:40px"><div style="width:18px;height:12px;margin:0 auto 2px;background:#2a9a3c"></div><div style="font-size:5px;font-weight:700">Description</div><div style="font-size:10px">9%</div><div class="tiny" style="font-size:3.5px">Just change the chart, and recolor a fill with your own.</div></div>
  <div class="line" style="left:116px;top:104px;width:1px;height:56px;background:var(--red)"></div>
  <div class="abs" style="left:194px;top:32px;text-align:center;width:40px"><div style="width:18px;height:12px;margin:0 auto 2px;background:linear-gradient(90deg,#2a9a3c 33%,#fff 33% 66%,var(--red) 66%)"></div><div style="font-size:5px;font-weight:700">Description</div><div style="font-size:10px">9%</div><div class="tiny" style="font-size:3.5px">Just change the chart, and recolor a fill with your own.</div></div>
  <div class="abs" style="left:282px;top:58px;text-align:center;width:40px"><div style="width:18px;height:12px;margin:0 auto 2px;background:#f2f2f2;border:1px solid #ddd"></div><div style="font-size:5px;font-weight:700">Description</div><div style="font-size:10px;color:var(--light)">9%</div><div class="tiny" style="font-size:3.5px">Just change the chart, and recolor a fill with your own.</div></div>
  <div class="line" style="left:302px;top:112px;width:1px;height:50px;background:var(--light)"></div>
  <div class="abs" style="left:340px;top:48px;text-align:center;width:40px"><div style="width:18px;height:12px;margin:0 auto 2px;background:repeating-linear-gradient(180deg,var(--red) 0 2px,#fff 2px 4px)"></div><div style="font-size:5px;font-weight:700">Description</div><div style="font-size:10px;color:var(--light)">9%</div><div class="tiny" style="font-size:3.5px">Just change the chart, and recolor a fill with your own.</div></div>
  <p class="copyright">© Copyright 2017 Larkspan Digital Systems. All rights reserved.</p>
  <span class="page-no">63</span>
</section>

<!-- Bus infographic -->
<section class="slide" style="left:4px;top:467px">
  <h2 class="slide-title">BUS INFOGRAPHIC</h2>
  <div class="brand"><span class="brand-dot"></span><span class="brand-name">LARKSPAN</span></div>
  <div class="abs" role="img" aria-label="Red bus illustration" style="left:27px;top:48px;width:118px;height:42px;border-radius:4px 12px 4px 4px;background:var(--red);display:flex;align-items:flex-end;justify-content:center;padding-bottom:8px;color:#fff;font-size:7px">Description</div>
  <div class="abs" role="img" aria-label="Black bus illustration" style="left:27px;top:102px;width:118px;height:42px;border-radius:4px 12px 4px 4px;background:var(--black);display:flex;align-items:flex-end;justify-content:center;padding-bottom:8px;color:#fff;font-size:7px">Description</div>
  <div class="abs" role="img" aria-label="Grey bus illustration" style="left:27px;top:156px;width:118px;height:42px;border-radius:4px 12px 4px 4px;background:var(--light);display:flex;align-items:flex-end;justify-content:center;padding-bottom:8px;color:#fff;font-size:7px">Description</div>
  <div class="abs" style="left:160px;top:56px;width:220px"><div style="font-size:5.5px;font-weight:700">Destination</div><div style="display:flex;gap:4px"><span class="red" style="font-size:13px;font-weight:700">30%</span><p class="tiny">For every 6 emails received, we get 3 Phone calls. Suitable for all categories business and personal presentation, Suitable for all categories business and personal presentation, feel free to edit it.</p></div></div>
  <div class="abs" style="left:160px;top:110px;width:220px"><div style="font-size:5.5px;font-weight:700">Destination</div><div style="display:flex;gap:4px"><span style="font-size:13px;font-weight:700">70%</span><p class="tiny">For every 6 emails received, we get 3 Phone calls. Suitable for all categories business and personal presentation, Suitable for all categories business and personal presentation, feel free to edit it.</p></div></div>
  <div class="abs" style="left:160px;top:164px;width:220px"><div style="font-size:5.5px;font-weight:700">Destination</div><div style="display:flex;gap:4px"><span style="font-size:13px;font-weight:700;color:var(--light)">98%</span><p class="tiny">For every 6 emails received, we get 3 Phone calls. Suitable for all categories business and personal presentation, Suitable for all categories business and personal presentation, feel free to edit it.</p></div></div>
  <p class="copyright">© Copyright 2017 Larkspan Digital Systems. All rights reserved.</p>
  <span class="page-no">64</span>
</section>

<!-- Car infographic -->
<section class="slide" style="left:402px;top:467px">
  <h2 class="slide-title">CAR INFOGRAPHIC</h2>
  <div class="brand"><span class="brand-dot"></span><span class="brand-name">LARKSPAN</span></div>
  <div class="abs" role="img" aria-label="Four cars with fading diagonal trails in red, black, dark grey and light grey" style="left:0;top:40px;width:230px;height:180px">
    <div class="abs" style="left:-30px;top:60px;width:210px;height:22px;transform:rotate(-40deg);background:linear-gradient(90deg,transparent,var(--red));border-radius:0 11px 11px 0"></div>
    <div class="abs" style="left:10px;top:80px;width:210px;height:22px;transform:rotate(-40deg);background:linear-gradient(90deg,transparent,var(--black));border-radius:0 11px 11px 0"></div>
    <div class="abs" style="left:-10px;top:118px;width:190px;height:22px;transform:rotate(-40deg);background:linear-gradient(90deg,transparent,var(--dark));border-radius:0 11px 11px 0"></div>
    <div class="abs" style="left:50px;top:118px;width:210px;height:22px;transform:rotate(-40deg);background:linear-gradient(90deg,transparent,var(--light));border-radius:0 11px 11px 0"></div>
  </div>
  <div class="abs" style="left:236px;top:56px;display:flex;gap:5px;align-items:flex-end"><span class="red" style="font-size:17px;font-weight:700">975</span><div style="width:108px"><div style="font-size:5.5px;font-weight:700">Million</div><p class="tiny">For every 6 emails received, we get 3 Phone calls.</p></div></div>
  <div class="abs" style="left:222px;top:90px;display:flex;gap:5px;align-items:flex-end"><span style="font-size:17px;font-weight:700">1,089</span><div style="width:108px"><div style="font-size:5.5px;font-weight:700">Million</div><p class="tiny">For every 6 emails received, we get 3 Phone calls.</p></div></div>
  <div class="abs" style="left:236px;top:124px;display:flex;gap:5px;align-items:flex-end"><span style="font-size:17px;font-weight:700;color:var(--dark)">825</span><div style="width:108px"><div style="font-size:5.5px;font-weight:700">Million</div><p class="tiny">For every 6 emails received, we get 3 Phone calls.</p></div></div>
  <div class="abs" style="left:222px;top:158px;display:flex;gap:5px;align-items:flex-end"><span style="font-size:17px;font-weight:700;color:var(--light)">1,257</span><div style="width:108px"><div style="font-size:5.5px;font-weight:700">Million</div><p class="tiny">For every 6 emails received, we get 3 Phone calls.</p></div></div>
  <p class="copyright">© Copyright 2017 Larkspan Digital Systems. All rights reserved.</p>
  <span class="page-no">65</span>
</section>

<!-- Plane infographic C -->
<section class="slide" style="left:800px;top:467px">
  <h2 class="slide-title">PLANE INFOGRAPHIC</h2>
  <div class="brand"><span class="brand-dot"></span><span class="brand-name">LARKSPAN</span></div>
  <div class="abs" style="left:18px;top:58px;width:170px"><div style="font-size:5.5px;font-weight:700">Popular destination</div><p class="tiny">For every 6 emails received, we get 3 Phone calls. Suitable for all categories business and personal presentation, Suitable for all categories business and personal presentation, feel free to edit it.</p></div>
  <div class="abs" style="left:18px;top:92px;width:170px;display:grid;grid-template-columns:1fr 1fr;gap:6px 10px">
    <div style="display:flex;gap:4px"><span style="width:16px;height:16px;border-radius:50%;background:linear-gradient(180deg,#111 33%,var(--red) 33% 66%,#f5c400 66%)"></span><div><div class="tiny">Description</div><div class="red" style="font-size:12px;font-weight:700">75</div><p class="tiny" style="font-size:3.5px">Click the shape on truck, ungroup it and recolor a fill with your own</p></div></div>
    <div style="display:flex;gap:4px"><span style="width:16px;height:16px;border-radius:50%;background:var(--red)"></span><div><div class="tiny">Description</div><div style="font-size:12px;font-weight:700;color:var(--dark)">67</div><p class="tiny" style="font-size:3.5px">Click the shape on truck, ungroup it and recolor a fill with your own</p></div></div>
    <div style="display:flex;gap:4px"><span style="width:16px;height:16px;border-radius:50%;background:linear-gradient(90deg,#2a9a3c 40%,var(--red) 40%)"></span><div><div class="tiny">Description</div><div style="font-size:12px;font-weight:700">112</div><p class="tiny" style="font-size:3.5px">Click the shape on truck, ungroup it and recolor a fill with your own</p></div></div>
    <div style="display:flex;gap:4px"><span style="width:16px;height:16px;border-radius:50%;background:var(--red)"></span><div><div class="tiny">Description</div><div style="font-size:12px;font-weight:700;color:var(--light)">175</div><p class="tiny" style="font-size:3.5px">Click the shape on truck, ungroup it and recolor a fill with your own</p></div></div>
  </div>
  <div class="abs" style="left:218px;top:107px;width:24px;text-align:center;font-size:11px;font-weight:700;color:var(--red)">55%</div>
  <div class="abs" role="img" aria-label="Red plane icon with trail" style="left:222px;top:124px;width:16px;height:86px;background:linear-gradient(180deg,var(--red),rgba(232,32,42,0))"></div>
  <div class="abs" style="left:252px;top:67px;width:24px;text-align:center;font-size:11px;font-weight:700">73%</div>
  <div class="abs" role="img" aria-label="Black plane icon with trail" style="left:256px;top:84px;width:16px;height:126px;background:linear-gradient(180deg,#111,#8aa2b0 60%,rgba(200,210,215,0))"></div>
  <div class="abs" style="left:286px;top:112px;width:24px;text-align:center;font-size:11px;font-weight:700;color:var(--dark)">43%</div>
  <div class="abs" role="img" aria-label="Grey plane icon with trail" style="left:290px;top:129px;width:16px;height:81px;background:linear-gradient(180deg,var(--mid),rgba(125,125,125,0))"></div>
  <div class="abs" style="left:320px;top:43px;width:24px;text-align:center;font-size:11px;font-weight:700;color:var(--light)">81%</div>
  <div class="abs" role="img" aria-label="Light grey plane icon with trail" style="left:324px;top:60px;width:16px;height:150px;background:linear-gradient(180deg,var(--light),rgba(183,183,183,0))"></div>
  <p class="copyright">© Copyright 2017 Larkspan Digital Systems. All rights reserved.</p>
  <span class="page-no">66</span>
</section>

</main>
</body>
</html>
```